Employment Agency Website Design

We are working with an employment agency in California.

Some sites to use for content/competitors and inspiration:

https://www.pinecrestjobs.com/us/en
https://www.velmorusa.com
https://www.dravenworks.us
https://www.quillora.com/en
https://www.tomvalusa.com
https://www.fernstaffing.com

Thank you for taking the time to consider designing a website for us. We are web developers based in Stockton, CA, USA. Most of our projects go through the same process. Understanding this process may help you win a project with us. We custom-code all of our websites in-house. We don’t have any requirements as to what tools you use for your design, but we prefer Figma files. For any design that we label as four-stars, we send it to the client for review. The client picks the final design they want us to use. Once we complete this process, we will continue to show additional clients all the four-star sites and purchase them later. Your designs will have multiple chances to sell. For better chances of success, we ask that you follow these guidelines.

IMAGES:
If you use any images or icons in the design, we ask that you have a link to the asset so we can purchase the image/icon. Most of the designs we submit do not have the customer’s images on them unless they have some great images. Be creative; show us the feeling you are trying to portray with your image choices. Use any royalty-free site you choose. We subscribe to Adobe and mainly use their images, but we can purchase images outside of Adobe. PLEASE NOTE: we will not submit designs to clients with watermarks on the images.

FONTS:
We ask that you identify the fonts used in the design. This can be done in a message if you want. We typically use plain client badge Fonts and Adobe Fonts.

CONTENT:
We're always open to different content and ideas. We often submit designs with stock images so the client can see our vision. We typically take pictures after the website launch to use their images with our vision. Lorem Ipsum is fine for paragraphs, but we ask that you write the headers in correct English. We want to be able to show the vision and identify the sections of the website.

INSPIRATION:
We typically add a couple of links in the brief of websites we like to help you get started in your design.

REVISIONS:
We do not often ask for revisions of the designs unless we see something in the design that may not appeal to the client. If there are slight changes that we want to make, we do that in the development process.

FEEDBACK:
We rarely give feedback on designs during the design process. We are working on many website projects and do not have the time to provide feedback. We usually respond if your request is well thought out and asks specific questions, but a note asking “feedback, please” usually goes unanswered.

```html
<!DOCTYPE html>
<html lang="en">
<head>
<meta charset="utf-8">
<title>Brightwell Talent – Website Mobile Version</title>
<link href="https://fonts.googleapis.com/css2?family=Poppins:wght@300;400;500;600&family=Space+Grotesk:wght@500;600;700&display=swap" rel="stylesheet">
<style>
  :root{
    --red:#c01f2e;
    --ink:#1b1b1f;
    --navy:#1f2a4f;
    --muted:#8a8d96;
    --soft:#f6f7f9;
    --line:#e7e8ec;
    --white:#ffffff;
    --sans:"Poppins",sans-serif;
    --display:"Space Grotesk",sans-serif;
  }
  *{box-sizing:border-box;margin:0;padding:0}
  html,body{width:1200px;height:800px;overflow:hidden;background:var(--white)}
  body{position:relative;font-family:var(--sans);color:var(--ink)}
  .abs{position:absolute}

  /* presentation intro */
  .brand-lockup{left:113px;top:346px}
  .brand-lockup .mark{position:absolute;left:0;top:6px;width:42px;height:42px;background:var(--red)}
  .brand-lockup .name{position:absolute;left:52px;top:0;font-size:29px;font-weight:500;color:var(--ink);white-space:nowrap;line-height:42px}
  .brand-lockup .tagline{position:absolute;left:53px;top:40px;font-size:11px;font-weight:300;color:#6b6b70;white-space:nowrap}
  .deck-title{left:100px;top:436px;font-family:var(--sans);font-weight:600;font-size:22px;letter-spacing:-.8px;white-space:nowrap}

  /* screens */
  .screen{position:absolute;overflow:hidden;background:var(--white)}
  .screen-faq{left:472px;top:0;width:193px;height:303px;background:var(--white)}
  .screen-steps{left:472px;top:332px;width:193px;height:468px}
  .screen-home{left:696px;top:0;width:194px;height:800px}
  .screen-paycheck{left:919px;top:0;width:193px;height:303px;background:var(--soft)}
  .screen-footer{left:919px;top:332px;width:193px;height:468px;background:var(--soft)}

  .small{font-size:7.5px;line-height:10px;color:var(--muted);font-weight:300}
  .pill{position:absolute;border-radius:20px;font-size:7.5px;font-weight:500;display:flex;align-items:center;justify-content:center}
  .pill-red{background:var(--red);color:var(--white)}
  .btn{position:absolute;display:flex;align-items:center;justify-content:center;gap:8px;font-size:8px;font-weight:500;border-radius:3px}
  .btn-red{background:var(--red);color:var(--white);box-shadow:0 3px 6px rgba(192,31,46,.2)}
  .btn svg{width:8px;height:8px}

  /* FAQ */
  .faq-title{left:10px;top:-6px;font-family:var(--display);font-weight:600;font-size:20px}
  .faq-item{position:absolute;left:10px;width:173px;border-bottom:1px solid var(--line);height:40px}
  .faq-item p{width:140px}
  .faq-item .plus{position:absolute;right:6px;top:3px;font-size:10px;color:var(--muted);font-weight:300}
  .btn-ghost{left:10px;top:167px;width:173px;height:37px;background:var(--soft);color:var(--ink);font-weight:400;font-size:7.5px}
  .faq-band{left:0;top:235px;width:193px;height:68px;background:var(--soft)}
  .pill-outline{left:66px;top:267px;width:60px;height:18px;border:1px solid var(--red);color:var(--red);background:var(--white)}

  /* steps */
  .steps-band{left:0;top:0;width:193px;height:234px;background:var(--soft)}
  .step-text{position:absolute;left:40px;width:113px;text-align:center;font-size:6.5px;line-height:10px}
  .step-num{position:absolute;left:81px;width:31px;height:31px;border-radius:50%;display:flex;align-items:center;justify-content:center;font-size:8px;font-weight:600}
  .step-num.active{background:var(--red);color:var(--white)}
  .step-num.idle{background:#e9eaee;color:var(--red)}
  .jobs-heading{left:10px;top:288px;width:180px;font-family:var(--display);font-weight:600;font-size:19.5px;line-height:26.5px}
  .tab{position:absolute;top:444px;height:25px;display:flex;align-items:center;font-family:var(--display);font-weight:600;font-size:11.5px;white-space:nowrap}
  .tab-active{left:15px;width:86px;justify-content:center;background:var(--white);border-radius:14px;box-shadow:0 2px 8px rgba(0,0,0,.06)}
  .tab-idle{left:118px;color:var(--muted)}

  /* home */
  .promo-strip{left:0;top:0;width:194px;height:7px;background:var(--red);color:var(--white);font-size:4px;line-height:5px;white-space:nowrap;overflow:hidden;padding-left:3px}
  .social{position:absolute;display:flex;gap:10px}
  .social span{width:10px;height:10px;border-radius:2px;background:currentColor}
  .social span.round{border-radius:50%}
  .topnav{position:absolute;top:18px;font-size:7px;color:var(--muted);font-weight:300}
  .logo-card{left:62px;top:46px;width:69px;height:31px;background:var(--white);box-shadow:0 4px 12px rgba(0,0,0,.07);border-radius:3px;display:flex;align-items:center;justify-content:center;gap:3px;font-size:5.5px;font-weight:500;color:var(--ink)}
  .logo-card i{width:6px;height:6px;background:var(--red);display:block}
  .hero-photo{left:130px;top:97px;width:64px;height:310px;border-radius:64px 0 0 64px;background:linear-gradient(160deg,#d63040 0%,#e2a230 45%,#f1b23b 70%,#3f5f8a 100%)}
  .hero-title{left:10px;top:114px;width:150px;font-family:var(--display);font-weight:700;font-size:25px;line-height:34.5px;color:var(--red)}
  .hero-copy{left:10px;top:304px;width:165px;font-size:8.7px;line-height:16px;color:#5f626b}
  .btn-hero{left:10px;top:368px;width:172px;height:37px;font-size:7.5px}
  .field{position:absolute;left:10px;width:172px;height:23px;background:var(--soft);border-radius:3px;display:flex;align-items:center;gap:6px;padding-left:14px;font-size:6.5px;color:var(--muted);font-weight:300}
  .field svg{width:8px;height:8px}
  .btn-search{left:10px;top:506px;width:172px;height:21px;font-size:7px}
  .trusted{left:0;top:569px;width:194px;height:85px;background:var(--soft);border-radius:6px}
  .trusted p{position:absolute;top:20px;width:100%;text-align:center;font-size:9px;color:#6b6e76}
  .client{position:absolute;top:50px;height:14px;background:#c9ccd4}
  .benefits{left:0;top:687px;width:194px;height:113px;background:linear-gradient(180deg,#3a4a63,#5b6880)}
  .benefits .pill{left:10px;top:31px;width:48px;height:18px}
  .benefits h3{position:absolute;left:10px;top:64px;font-family:var(--display);font-weight:600;font-size:20.5px;line-height:27px;color:var(--white);white-space:nowrap}
  .benefits h3 u{text-decoration-color:var(--red);text-decoration-thickness:2px;text-underline-offset:1px}

  /* paycheck */
  .dots{left:0;top:32px;width:193px;display:flex;justify-content:center;gap:5px}
  .dots span{width:3px;height:3px;border-radius:50%;border:0.7px solid var(--ink)}
  .dots span.on{background:var(--ink)}
  .pay-photo{left:0;top:68px;width:193px;height:190px;background:linear-gradient(135deg,#e6e8ec 0%,#cdd3dc 55%,#4a6794 100%)}
  .pay-card{left:10px;top:100px;width:172px;height:127px;background:var(--soft)}
  .pay-card h3{position:absolute;top:16px;width:100%;text-align:center;font-family:var(--sans);font-weight:500;font-size:13.5px;line-height:20px;color:var(--navy)}
  .pay-card .btn{left:10px;top:73px;width:152px;height:37px;font-size:8px}
  .pay-brand{left:14px;top:292px;font-size:14px;font-weight:500;color:var(--ink);white-space:nowrap}

  /* footer */
  .foot-copy{left:10px;top:-4px;font-size:7px;line-height:15px;color:var(--ink);font-weight:300}
  .foot-col{position:absolute;left:10px;font-size:7px;color:var(--muted);font-weight:300}
  .foot-col.head{color:var(--ink);font-weight:600;font-size:6.8px}
  .copyright{left:0;top:443px;width:193px;text-align:center;font-size:6.5px;color:var(--ink);font-weight:300;letter-spacing:-.2px}
</style>
</head>
<body>

  <!-- intro -->
  <div class="abs brand-lockup">
    <span class="mark"></span>
    <span class="name">Brightwell Talent</span>
    <span class="tagline">The future of work.</span>
  </div>
  <h1 class="abs deck-title">WEBSITE MOBILE VERSION</h1>

  <!-- FAQ screen -->
  <section class="screen screen-faq">
    <h2 class="abs faq-title">Questions</h2>
    <div class="faq-item" style="top:38px"><p class="small">Lorem Ipsum is simply dummy text of the printing and typesetting industry.</p><span class="plus">+</span></div>
    <div class="faq-item" style="top:80px"><p class="small">Lorem Ipsum is simply dummy text of the printing and typesetting</p><span class="plus">+</span></div>
    <div class="faq-item" style="top:122px"><p class="small">Lorem Ipsum is simply dummy text of the printing and typesetting industry.</p><span class="plus">+</span></div>
    <a class="btn btn-ghost">Contact Us
      <svg viewBox="0 0 8 8"><path d="M3 1.5 5.5 4 3 6.5" fill="none" stroke="currentColor" stroke-width="1"/></svg>
    </a>
    <div class="abs faq-band"></div>
    <span class="pill pill-outline">Testimonial</span>
  </section>

  <!-- steps & jobs screen -->
  <section class="screen screen-steps">
    <div class="abs steps-band"></div>
    <p class="step-text small" style="top:2px">Lorem Ipsum is simply dummy text of the printing and typesetting industry.</p>
    <span class="step-num active" style="top:50px">III</span>
    <p class="step-text small" style="top:96px">Lorem Ipsum is simply dummy text of the printing and typesetting industry.</p>
    <span class="step-num idle" style="top:144px">IV</span>
    <p class="step-text small" style="top:190px">Lorem Ipsum is simply dummy text of the printing and typesetting industry.</p>
    <span class="pill pill-red" style="left:10px;top:266px;width:83px;height:18px">Job Recomended</span>
    <h2 class="abs jobs-heading">Add specialized talent across your organization</h2>
    <span class="tab tab-active">Designer</span>
    <span class="tab tab-idle">Administrative</span>
  </section>

  <!-- home screen -->
  <section class="screen screen-home">
    <div class="abs promo-strip">Lorem Ipsum is simply dummy text of the printing and typesetting industry.</div>
    <div class="social" style="left:10px;top:18px;color:#8a94a6"><span></span><span class="round"></span><span class="round"></span></div>
    <span class="topnav" style="left:96px">Privacy Policy</span>
    <span class="topnav" style="left:154px">Eng ⌄</span>
    <div class="abs logo-card"><i></i>Brightwell Talent</div>
    <div class="abs hero-photo" role="img" aria-label="Smiling woman in a mustard sweater against a red circle"></div>
    <h2 class="abs hero-title">Anything’s possible when you have the talent</h2>
    <p class="abs hero-copy">Find skilled candidates, in-demand jobs and the solutions you need to help you do your best work yet.</p>
    <a class="btn btn-red btn-hero">Find Your Job Now
      <svg viewBox="0 0 8 8"><path d="M1 4h6M4.5 1.5 7 4 4.5 6.5" fill="none" stroke="currentColor" stroke-width="0.9"/></svg>
    </a>
    <div class="field" style="top:446px">
      <svg viewBox="0 0 8 8"><circle cx="3.3" cy="3.3" r="2.3" fill="none" stroke="#8a8d96" stroke-width="0.8"/><path d="M5 5l2.3 2.3" stroke="#8a8d96" stroke-width="0.8"/></svg>
      Job Title, Skills, or Keywords
    </div>
    <div class="field" style="top:476px">
      <svg viewBox="0 0 8 8"><path d="M4 7.5S1.3 4.8 1.3 3.1a2.7 2.7 0 0 1 5.4 0C6.7 4.8 4 7.5 4 7.5z" fill="none" stroke="#8a8d96" stroke-width="0.8"/><circle cx="4" cy="3.1" r="0.9" fill="#8a8d96"/></svg>
      City, State, Or Zip Code
    </div>
    <a class="btn btn-red btn-search">Search Job</a>
    <div class="abs trusted">
      <p>Trusted by many companies.</p>
      <span class="client" style="left:12px;width:14px;border-radius:50%"></span>
      <span class="client" style="left:46px;width:14px;border-radius:2px"></span>
      <span class="client" style="left:80px;width:26px;border-radius:2px"></span>
      <span class="client" style="left:128px;width:46px;border-radius:10px"></span>
    </div>
    <div class="abs benefits" role="img" aria-label="Photo of a consultant at work in an office">
      <span class="pill pill-red">Benefits</span>
      <h3><u>Consulting</u><br>solutions to</h3>
    </div>
  </section>

  <!-- paycheck screen -->
  <section class="screen screen-paycheck">
    <div class="abs dots"><span></span><span></span><span class="on"></span><span></span><span></span></div>
    <div class="abs pay-photo" role="img" aria-label="Photo of a person in a blue suit walking"></div>
    <div class="abs pay-card">
      <h3>Questions about your<br>paycheck?</h3>
      <a class="btn btn-red">Contact Us
        <svg viewBox="0 0 8 8"><path d="M3 1.5 5.5 4 3 6.5" fill="none" stroke="currentColor" stroke-width="1"/></svg>
      </a>
    </div>
    <span class="abs pay-brand">Brightwell Talent</span>
  </section>

  <!-- footer screen -->
  <section class="screen screen-footer">
    <p class="abs foot-copy">standard dummy text ever since the<br>1500s.</p>
    <div class="social" style="left:10px;top:35px;color:var(--ink)"><span></span><span class="round"></span><span class="round"></span></div>
    <span class="foot-col head" style="top:117px">Service</span>
    <span class="foot-col" style="top:142px">Browse Job</span>
    <span class="foot-col" style="top:163px">Contract Talent</span>
    <span class="foot-col" style="top:184px">Consulting Solutions</span>
    <span class="foot-col head" style="top:211px">Contact</span>
    <span class="foot-col" style="top:236px">Email</span>
    <span class="foot-col" style="top:257px">Phone</span>
    <span class="foot-col" style="top:278px">Location</span>
    <span class="foot-col" style="top:299px">Newsletter</span>
    <span class="foot-col head" style="top:325px">About Us</span>
    <span class="foot-col" style="top:350px">Brightwell Talent</span>
    <span class="foot-col" style="top:371px">Pengembang</span>
    <span class="foot-col" style="top:392px">Jobs</span>
    <p class="abs copyright">© 2024 Brightwell Talent. All rights reserved.</p>
  </section>

</body>
</html>
```